i need a business card for a plumbing company in california

we are a drain cleaning , maintenance plumbing company who is starting new marketing campaign for a tatrench-less pipe installation department .

Target Market(s)

the professional who appreciates time and quality workmanship.

Industry/Entity Type

Plumbing

Colors
0655a3
ec1f27

Requirements
Must have
• the second logo needs to be included
Nice to have
• a focus on the services offered
Should not have
• any underlined words on the brief

```html
<!DOCTYPE html>
<html lang="en">
<head>
<meta charset="utf-8">
<title>Flowline Plumbing – Business Card</title>
<link href="https://fonts.googleapis.com/css2?family=Arimo:wght@400;700&display=swap" rel="stylesheet">
<style>
  :root{
    --brand-blue:#0655a3;
    --brand-blue-deep:#0a3f7e;
    --brand-red:#ec1f27;
    --card-white:#f4f4f2;
    --logo-grey:#5e5e5e;
    --backdrop:#2b2b2b;
    --text-light:#ffffff;
  }
  *{margin:0;padding:0;box-sizing:border-box}
  html,body{width:1200px;height:997px;overflow:hidden}
  body{
    background:var(--backdrop);
    font-family:"Arimo",Arial,sans-serif;
    position:relative;
  }
  .card{
    position:absolute;
    width:540px;height:310px;
    border-radius:18px;
    overflow:hidden;
    background:var(--card-white);
    box-shadow:0 18px 40px rgba(0,0,0,.55);
  }
  .card svg.card-art{position:absolute;inset:0;width:100%;height:100%}
  .card--back{left:40px;top:200px}
  .card--front{left:620px;top:487px}

  .brand{
    position:absolute;
    display:flex;align-items:center;gap:10px;
  }
  .brand-name{
    font-weight:700;
    font-size:30px;
    color:var(--logo-grey);
    line-height:1.02;
    text-align:right;
    white-space:nowrap;
  }
  .brand-mark{
    display:block;
    width:30px;height:30px;
    background:var(--brand-red);
    border-radius:4px;
  }
  .card--back .brand{right:40px;top:26px}
  .card--front .brand{right:40px;top:48px}

  .website{
    position:absolute;right:40px;top:126px;
    font-weight:700;font-size:14px;letter-spacing:.5px;
    color:var(--brand-blue);
  }

  .services{
    position:absolute;left:40px;top:172px;
    color:var(--text-light);
  }
  .services-title{
    font-weight:700;font-size:15px;
    color:var(--brand-red);
    font-variant:small-caps;letter-spacing:.5px;
    margin-bottom:10px;
  }
  .services-list{list-style:none}
  .services-item{
    display:flex;align-items:center;gap:10px;
    font-size:12px;letter-spacing:.6px;text-transform:uppercase;
    margin-bottom:9px;
  }
  .services-bullet{
    width:20px;height:20px;border-radius:5px;
    background:var(--brand-red);flex:none;
  }

  .person{position:absolute;left:40px;top:122px}
  .person-name{
    font-weight:700;font-size:16px;letter-spacing:.5px;
    color:var(--brand-red);text-transform:uppercase;
  }
  .person-role{font-size:13px;color:var(--text-light);margin:4px 0 0 42px}

  .contact{position:absolute;left:46px;bottom:34px;list-style:none}
  .contact-item{
    display:flex;align-items:center;gap:9px;
    color:var(--text-light);font-size:14px;
    margin-top:10px;
  }
  .contact-icon{width:18px;height:18px;flex:none}
</style>
</head>
<body>

  <section class="card card--back" aria-label="Card back">
    <svg class="card-art" viewBox="0 0 540 310" preserveAspectRatio="none" aria-hidden="true">
      <path d="M0,152 C140,110 330,210 540,132 L540,310 L0,310 Z" fill="var(--brand-blue)"/>
      <path d="M0,152 C140,110 330,210 540,132 L540,146 C330,224 140,128 0,170 Z" fill="var(--brand-blue-deep)" opacity=".35"/>
      <path d="M-10,142 C150,96 330,196 545,116" fill="none" stroke="var(--brand-red)" stroke-width="6" stroke-linecap="round"/>
    </svg>
    <div class="brand">
      <span class="brand-name">Flowline<br>Plumbing</span>
      <span class="brand-mark"></span>
    </div>
    <div class="services">
      <h2 class="services-title">Our Services</h2>
      <ul class="services-list">
        <li class="services-item"><span class="services-bullet"></span>Sewer Drain Cleaning</li>
        <li class="services-item"><span class="services-bullet"></span>Maintenance</li>
        <li class="services-item"><span class="services-bullet"></span>Trenchless Pipe Installs</li>
      </ul>
    </div>
  </section>

  <section class="card card--front" aria-label="Card front">
    <svg class="card-art" viewBox="0 0 540 310" preserveAspectRatio="none" aria-hidden="true">
      <path d="M0,0 L50,0 C160,30 230,170 330,240 C370,270 400,295 425,310 L0,310 Z" fill="var(--brand-blue)"/>
      <path d="M42,-4 C175,22 245,160 345,228 C390,260 450,285 540,296" fill="none" stroke="var(--brand-red)" stroke-width="7" stroke-linecap="round"/>
    </svg>
    <div class="brand">
      <span class="brand-name">Flowline<br>Plumbing</span>
      <span class="brand-mark"></span>
    </div>
    <p class="website">www.flowlineplumbing.com</p>

    <div class="person">
      <p class="person-name">Mateo Serrano</p>
      <p class="person-role">Director</p>
    </div>

    <ul class="contact">
      <li class="contact-item">
        <svg class="contact-icon" viewBox="0 0 18 18" aria-hidden="true">
          <circle cx="9" cy="9" r="9" fill="var(--brand-red)"/>
          <path d="M6 4.5c.6 0 1 1.6 1.2 2.2.1.5-.8.9-.6 1.4.4 1 1.3 1.9 2.3 2.3.5.2.9-.7 1.4-.6.6.2 2.2.6 2.2 1.2 0 .8-.9 1.6-1.8 1.5C8 12.2 5.8 10 5.5 6.3 5.4 5.4 5.2 4.5 6 4.5z" fill="#fff"/>
        </svg>
        1300555019
      </li>
      <li class="contact-item">
        <svg class="contact-icon" viewBox="0 0 18 18" aria-hidden="true">
          <circle cx="9" cy="9" r="9" fill="var(--brand-red)"/>
          <rect x="4.5" y="5.5" width="9" height="7" rx="1" fill="#fff"/>
          <path d="M4.8 6 9 9.3 13.2 6" fill="none" stroke="var(--brand-red)" stroke-width="1"/>
        </svg>
        hello@flowlineplumbing.com
      </li>
    </ul>
  </section>

</body>
</html>
```